Harrowgate Care Assurance Ltd needs a business card and logo

We need a logo for documents, invoices etc and a business card to match. We are a health auditing, training and consulting company based in NZ and working in both Australia and NZ. We ensure health organisations meet all their compliance requirements and develop expertise in the health auditing sector. The design should in some way reflect either symbols for quality management in the health sector.

Target Market(s)

Health providers and those wishing to increase their capability in meeting and understanding compliance requirements

Industry/Entity Type

Business

Contact Information for Business Card

Logo plus contact details

Logo Text

Health auditing, consultancy and training

Requirements
Must have
• Name and contact details director: Marla Fenwick, mfenwick@hca-example.co.nz, PO Box 318, Kerrowby, NZ, cell +6427391652

```html
<!DOCTYPE html>
<html lang="en">
<head>
<meta charset="utf-8">
<title>Harrowgate Care Assurance Ltd – Business Card</title>
<link href="https://fonts.googleapis.com/css2?family=Open+Sans:wght@400;600;700&display=swap" rel="stylesheet">
<style>
  :root {
    --stage: #e9e7e6;
    --card-top-light: #fbfafa;
    --card-top-shade: #eeeaea;
    --band-top: #08c2ee;
    --band-bottom: #0660c2;
    --brand-blue: #1a86d8;
    --text-light: #ffffff;
  }
  * { margin: 0; padding: 0; box-sizing: border-box; }
  html, body {
    width: 1200px;
    height: 900px;
    overflow: hidden;
    background: var(--stage);
    font-family: "Open Sans", Arial, sans-serif;
  }
  .canvas {
    position: relative;
    width: 1200px;
    height: 900px;
  }
  .business-card {
    position: absolute;
    left: 110px;
    top: 147px;
    width: 980px;
    height: 606px;
    overflow: hidden;
    box-shadow: 0 10px 30px rgba(0,0,0,0.15);
  }
  .card-brand {
    height: 326px;
    background: linear-gradient(180deg, var(--card-top-light), var(--card-top-shade));
    display: flex;
    align-items: center;
    justify-content: center;
    gap: 14px;
  }
  .brand-dot {
    width: 20px;
    height: 20px;
    border-radius: 50%;
    background: var(--brand-blue);
  }
  .brand-name {
    color: var(--brand-blue);
    font-weight: 600;
    font-size: 36px;
    letter-spacing: 0.5px;
  }
  .card-contact {
    position: relative;
    height: 280px;
    background: linear-gradient(180deg, var(--band-top), var(--band-bottom));
    color: var(--text-light);
  }
  .person {
    position: absolute;
    right: 575px;
    top: 98px;
    text-align: right;
  }
  .person-name {
    font-weight: 700;
    font-size: 31px;
    line-height: 1.1;
  }
  .person-role {
    font-size: 24px;
    line-height: 1.4;
  }
  .contact-list {
    position: absolute;
    left: 447px;
    top: 68px;
    list-style: none;
    font-size: 24px;
  }
  .contact-item {
    display: flex;
    align-items: center;
    gap: 14px;
    height: 34px;
  }
  .contact-icon { width: 20px; height: 22px; flex: none; }
  .contact-address { margin-top: 34px; }
</style>
</head>
<body>
<main class="canvas">
  <article class="business-card">
    <header class="card-brand">
      <span class="brand-dot" aria-hidden="true"></span>
      <h1 class="brand-name">Harrowgate Care Assurance Ltd</h1>
    </header>
    <section class="card-contact">
      <div class="person">
        <p class="person-name">Marla Fenwick</p>
        <p class="person-role">Director</p>
      </div>
      <ul class="contact-list">
        <li class="contact-item">
          <svg class="contact-icon" viewBox="0 0 20 22" aria-hidden="true">
            <rect x="5" y="2" width="10" height="18" rx="2" fill="none" stroke="#fff" stroke-width="2"/>
            <circle cx="10" cy="16.5" r="1.2" fill="#fff"/>
          </svg>
          <span>+6427391652</span>
        </li>
        <li class="contact-item">
          <svg class="contact-icon" viewBox="0 0 24 24" aria-hidden="true">
            <path fill="#fff" d="M6.6 10.8c1.4 2.8 3.8 5.1 6.6 6.6l2.2-2.2c.3-.3.7-.4 1-.2 1.1.4 2.3.6 3.6.6.6 0 1 .4 1 1V20c0 .6-.4 1-1 1C10.6 21 3 13.4 3 4c0-.6.4-1 1-1h3.5c.6 0 1 .4 1 1 0 1.3.2 2.5.6 3.6.1.3 0 .7-.2 1l-2.3 2.2z"/>
          </svg>
          <span>mfenwick@hca-example.co.nz</span>
        </li>
        <li class="contact-item contact-address">
          <span>PO Box 318, Kerrowby, NZ</span>
        </li>
      </ul>
    </section>
  </article>
</main>
</body>
</html>
```